New Business Card Design Project

Need a design that will create an impact / strong impression towards our clients for our business. We are in the lighting business and we do lighting retrofits for large commercial to industrial clientele.

Target Market(s)

Lighting Industry

Industry/Entity Type

Business

Font styles to use
Other font styles liked:
• we would like to use the font on our logo, not sure what it is though..

Requirements
Must have
• Our logo.
Nice to have
• We are open to suggestions that have to do with lighting.

```html
<!DOCTYPE html>
<html lang="en">
<head>
<meta charset="utf-8">
<title>Brightline Retrofit Co. — Business Card</title>
<link href="https://fonts.googleapis.com/css2?family=Roboto:wght@400;500&display=swap" rel="stylesheet">
<style>
  :root {
    --backdrop: #5a4838;
    --forest: #10340f;
    --leaf: #0b7a35;
    --lime: #6cc35a;
    --title-green: #1f8f3a;
    --paper: #f1f1f1;
    --ink-light: #f4f4f4;
  }
  * { box-sizing: border-box; margin: 0; padding: 0; }
  html, body { width: 1200px; height: 960px; overflow: hidden; }
  body {
    background: var(--backdrop);
    font-family: "Roboto", Arial, sans-serif;
    position: relative;
  }
  .card {
    position: absolute;
    width: 600px;
    height: 343px;
    box-shadow: 1px 2px 4px rgba(0,0,0,0.45);
    overflow: hidden;
  }
  .card-front { left: 314px; top: 113px; background: var(--forest); }
  .card-back { left: 312px; top: 472px; background: var(--forest); }

  .holder { position: absolute; left: 42px; top: 44px; }
  .holder-name { color: var(--title-green); font-size: 22px; font-weight: 500; letter-spacing: 0.2px; }
  .holder-role { color: var(--lime); font-size: 15px; font-weight: 500; margin-top: 3px; }

  .address { position: absolute; left: 42px; top: 161px; color: var(--ink-light); font-size: 14.5px; line-height: 18px; }
  .contacts { position: absolute; left: 42px; top: 207px; list-style: none; color: var(--ink-light); font-size: 14.5px; }
  .contacts li { display: flex; align-items: center; height: 19.2px; white-space: nowrap; }
  .contacts svg { width: 14px; height: 14px; margin-right: 9px; fill: var(--lime); flex: none; }

  .brand-panel {
    position: absolute; left: 279px; top: 0; width: 307px; height: 343px;
    background: var(--paper);
    display: flex; align-items: center; justify-content: center;
  }
  .brand-name { color: var(--forest); font-size: 21px; font-weight: 500; display: flex; align-items: center; gap: 10px; }
  .brand-mark { width: 14px; height: 14px; background: var(--leaf); }

  .edge-strip { position: absolute; left: 586px; top: 0; width: 14px; height: 343px; display: flex; flex-direction: column; }
  .edge-strip span { flex: 1; }
  .edge-strip .seg-dark { background: var(--forest); border-bottom: 1px solid var(--paper); }
  .edge-strip .seg-mid { background: var(--leaf); border-bottom: 1px solid var(--paper); }
  .edge-strip .seg-light { background: var(--lime); }

  .back-name {
    position: absolute; left: 0; right: 0; top: 150px; text-align: center;
    color: var(--ink-light); font-size: 30px; font-weight: 500;
    display: flex; align-items: center; justify-content: center; gap: 14px;
  }
  .back-name .brand-mark { width: 20px; height: 20px; background: var(--lime); }
  .back-web {
    position: absolute; left: 0; right: 0; top: 282px; text-align: center;
    color: var(--ink-light); font-size: 14.5px; letter-spacing: 3px;
  }
</style>
</head>
<body>
  <section class="card card-front">
    <div class="holder">
      <p class="holder-name">MARCUS REED</p>
      <p class="holder-role">CEO/FOUNDER</p>
    </div>
    <p class="address">418 Cedar Hollow Road<br>Fairbanks, Alaska 99701</p>
    <ul class="contacts">
      <li><svg viewBox="0 0 16 16" aria-hidden="true"><path d="M3 1l3 0 1 4-2 1.5c1 2 2.5 3.5 4.5 4.5L11 9l4 1v3c0 1-1 2-2 2C7 15 1 9 1 3c0-1 1-2 2-2z"/></svg>907 555 0142</li>
      <li><svg viewBox="0 0 16 16" aria-hidden="true"><path d="M4 0h8v16H4zM5.5 2v10h5V2zM7 13.3h2v1.4H7z" fill-rule="evenodd"/></svg>907 555 0187</li>
      <li><svg viewBox="0 0 16 16" aria-hidden="true"><path d="M4 1h8v4H4zM1 6h14v6h-3v3H4v-3H1zM5 10v4h6v-4z" fill-rule="evenodd"/></svg>907 555 0163</li>
      <li><svg viewBox="0 0 16 16" aria-hidden="true"><path d="M1 3h14v10H1zM2.5 4.5L8 8.5l5.5-4z" fill-rule="evenodd"/></svg>marcus@brightline.co</li>
      <li><svg viewBox="0 0 16 16" aria-hidden="true"><circle cx="8" cy="8" r="7"/><path d="M4 5c2 0 2 2 4 2s1 3 3 3" stroke="#10340f" stroke-width="1.4" fill="none"/></svg>www.brightline.co</li>
    </ul>
    <div class="brand-panel">
      <p class="brand-name"><span class="brand-mark"></span>Brightline Retrofit Co.</p>
    </div>
    <div class="edge-strip">
      <span class="seg-dark"></span><span class="seg-mid"></span><span class="seg-light"></span>
    </div>
  </section>

  <section class="card card-back">
    <p class="back-name"><span class="brand-mark"></span>Brightline Retrofit Co.</p>
    <p class="back-web">www.brightlineretrofit.com</p>
  </section>
</body>
</html>
```